Design a New Business Card for Our Company

We are looking for fresh, unique, and a modern business card that reflects our roots as digital marketing agency focused on SEM.

Industry/Entity Type

Marketing

Contact Information for Business Card

looking for very unique out of the box designs. clean and modern that compliments our logo

Requirements
Must have
• colors should match our logo
• Front should have name, address, email, and phone/fax of the person, phone/fax are the same number
• back should have our url

```html
<!DOCTYPE html>
<html lang="en">
<head>
<meta charset="utf-8">
<title>Brightpath Digital – Business Card</title>
<link href="https://fonts.googleapis.com/css2?family=Open+Sans:wght@400;600;700&display=swap" rel="stylesheet">
<style>
  :root {
    --brand-blue: #4a8bd0;
    --brand-blue-back: #5594d1;
    --ink-grey: #8a8d90;
    --stripe-grey: #a9abad;
    --card-white: #ffffff;
    --backdrop: #eceef0;
  }
  * { margin: 0; padding: 0; box-sizing: border-box; }
  html, body {
    width: 1200px; height: 900px; overflow: hidden;
    background: var(--backdrop);
    font-family: "Open Sans", Arial, sans-serif;
  }
  .card {
    position: absolute;
    width: 560px; height: 320px;
    box-shadow: 0 10px 28px rgba(0,0,0,.18);
    overflow: hidden;
  }

  /* Front */
  .card-front { left: 580px; top: 80px; background: var(--card-white); }
  .front-brand {
    position: absolute; left: 44px; top: 142px;
    display: flex; align-items: center; gap: 12px;
  }
  .brand-dot {
    width: 30px; height: 30px; border-radius: 50%;
    background: var(--brand-blue);
  }
  .brand-name {
    font-size: 28px; font-weight: 600; color: var(--ink-grey);
    letter-spacing: -0.3px;
  }
  .contact-block {
    position: absolute; right: 26px; top: 34px;
    text-align: right; color: var(--ink-grey);
    font-size: 13px; line-height: 17px;
  }
  .person-name { font-size: 19px; font-weight: 700; color: var(--brand-blue); line-height: 22px; }
  .person-role { font-size: 12px; margin-bottom: 14px; }
  .company-name { color: var(--brand-blue); font-size: 13.5px; }
  .address { margin-bottom: 12px; }
  .contact-line {
    display: flex; justify-content: flex-end; align-items: center; gap: 6px;
    height: 19px;
  }
  .contact-icon { width: 15px; height: 15px; flex: none; }
  .contact-line.no-icon { padding-right: 21px; }

  .base-stripe {
    position: absolute; left: 0; right: 0; bottom: 16px; height: 8px;
    background: var(--stripe-grey);
  }
  .base-stripe .accent {
    position: absolute; left: 66%; right: 4%; top: 0; bottom: 0;
    background: var(--brand-blue);
    border-left: 3px solid var(--card-white);
    border-right: 3px solid var(--card-white);
  }

  /* Back */
  .card-back { left: 70px; top: 470px; background: var(--brand-blue-back); }
  .back-brand {
    position: absolute; left: 0; right: 0; top: 118px;
    text-align: center;
    font-size: 40px; font-weight: 600; color: var(--card-white);
    letter-spacing: -0.5px;
  }
  .back-url {
    position: absolute; left: 0; right: 0; bottom: 46px;
    text-align: center;
    font-size: 16px; color: var(--card-white); letter-spacing: 0.3px;
  }
</style>
</head>
<body>

<section class="card card-front" aria-label="Business card front">
  <div class="front-brand">
    <span class="brand-dot"></span>
    <span class="brand-name">Brightpath Digital</span>
  </div>

  <div class="contact-block">
    <p class="person-name">Dana Whitfield</p>
    <p class="person-role">Owner</p>
    <p class="company-name">Brightpath Digital</p>
    <p class="address">N. 12 Maple Avenue, Suite 200,<br>Boise, ID 83702</p>

    <p class="contact-line">208.555.0147
      <svg class="contact-icon" viewBox="0 0 16 16" aria-label="phone"><circle cx="8" cy="8" r="8" fill="#4a8bd0"/><path d="M5 4.5c.6-.4 1.1-.3 1.4.2l.6 1.1c.2.4 0 .8-.3 1l-.4.3c.4.9 1.1 1.7 2 2.1l.3-.4c.3-.3.7-.4 1-.2l1.1.6c.5.3.6.8.2 1.4-.5.7-1.3.9-2.1.6C6.8 10.6 5.4 9.2 4.8 7.2c-.3-.9-.2-2 .2-2.7z" fill="#fff"/></svg>
    </p>
    <p class="contact-line">208.555.0147
      <svg class="contact-icon" viewBox="0 0 16 16" aria-label="fax"><circle cx="8" cy="8" r="8" fill="#4a8bd0"/><rect x="5.5" y="4" width="5" height="3" fill="#fff"/><rect x="4" y="7" width="8" height="4" rx="1" fill="#fff"/><rect x="5.5" y="10" width="5" height="2" fill="#4a8bd0" stroke="#fff" stroke-width=".8"/></svg>
    </p>
    <p class="contact-line">info@brightpathdigital.com
      <svg class="contact-icon" viewBox="0 0 16 16" aria-label="email"><circle cx="8" cy="8" r="8" fill="#4a8bd0"/><rect x="4" y="5.2" width="8" height="5.6" rx=".6" fill="#fff"/><path d="M4.3 5.6L8 8.4l3.7-2.8" fill="none" stroke="#4a8bd0" stroke-width=".9"/></svg>
    </p>
    <p class="contact-line">www.brightpathdigital.com
      <svg class="contact-icon" viewBox="0 0 16 16" aria-label="website"><circle cx="8" cy="8" r="8" fill="#4a8bd0"/><circle cx="8" cy="8" r="4" fill="none" stroke="#fff" stroke-width=".9"/><ellipse cx="8" cy="8" rx="1.8" ry="4" fill="none" stroke="#fff" stroke-width=".9"/><path d="M4 8h8" stroke="#fff" stroke-width=".9"/></svg>
    </p>
  </div>

  <div class="base-stripe"><span class="accent"></span></div>
</section>

<section class="card card-back" aria-label="Business card back">
  <p class="back-brand">Brightpath Digital</p>
  <p class="back-url">www.brightpathdigital.com</p>
</section>

</body>
</html>
```